BRIGHT RIVER POWER.

I'd like my business logo.
contact name: Dennis Halvorsen
phone:0438759164
email: info@brightriverpower.net.au
website: www.brightriverpower.net.au

services:
solar
battery storage
LED lighting
energy saving solutions
general electrical
I'd like the design to look professional

Target Market(s)

Everyone

Industry/Entity Type

Business

Contact Information for Business Card

as described above

Requirements
Must have
• Id like the colours and the design to work well with my logo.

```html
<!DOCTYPE html>
<html lang="en">
<head>
<meta charset="utf-8">
<title>Bright River Power – Business Card</title>
<link rel="stylesheet" href="https://fonts.googleapis.com/css2?family=Arimo:wght@400;700&display=swap">
<style>
  :root {
    --backdrop: #2a2a2a;
    --card-white: #f7f7f7;
    --card-white-shade: #e4e4e4;
    --green-light: #74ac45;
    --green-dark: #5c8d2a;
    --green-brand: #4f9a2e;
    --sun-orange: #f0a21c;
    --ink: #1f2a14;
    --soft-white: #e6f0da;
    --white: #ffffff;
  }
  * { box-sizing: border-box; margin: 0; padding: 0; }
  html, body { width: 1200px; height: 997px; overflow: hidden; }
  body {
    background: var(--backdrop);
    font-family: "Arimo", Arial, sans-serif;
    display: flex;
    align-items: center;
    justify-content: center;
  }
  .business-card {
    position: relative;
    width: 840px;
    height: 480px;
    border-radius: 26px;
    overflow: hidden;
    background: linear-gradient(180deg, var(--white) 0%, var(--card-white) 60%, var(--card-white-shade) 100%);
    box-shadow: 0 18px 40px rgba(0,0,0,0.55);
  }
  .accent-stripe {
    position: absolute; left: 0; right: 0; top: 192px; height: 9px;
    background: var(--green-brand);
  }
  .green-panel {
    position: absolute; left: 0; right: 0; top: 212px; bottom: 0;
    background: linear-gradient(135deg, var(--green-light) 0%, var(--green-dark) 100%);
  }
  .panel-notch {
    position: absolute; left: 62px; top: 211px; width: 36px; height: 20px;
  }
  .brand {
    position: absolute; left: 0; right: 0; top: 78px;
    display: flex; align-items: center; justify-content: center; gap: 16px;
    padding-left: 40px;
  }
  .brand-dot {
    width: 54px; height: 54px; border-radius: 50%;
    background: var(--sun-orange);
  }
  .brand-name {
    font-size: 40px; font-weight: 700; color: var(--green-brand);
    letter-spacing: 0.5px;
  }
  .contact-person { position: absolute; left: 60px; top: 246px; }
  .person-name { font-size: 24px; font-weight: 700; color: var(--ink); }
  .person-role { font-size: 18px; color: var(--soft-white); margin-top: 4px; }
  .contact-list {
    position: absolute; left: 60px; top: 318px;
    list-style: none; display: flex; flex-direction: column; gap: 18px;
  }
  .contact-item {
    display: flex; align-items: center; gap: 14px;
    font-size: 21px; color: var(--ink);
  }
  .contact-icon { width: 24px; height: 24px; flex: none; }
  .services {
    position: absolute; right: 46px; top: 238px;
    text-align: right; list-style: none;
    font-size: 20px; line-height: 34px; color: var(--white);
  }
  .services-title { color: var(--soft-white); opacity: 0.85; }
</style>
</head>
<body>
  <main class="business-card">
    <div class="brand">
      <span class="brand-dot"></span>
      <span class="brand-name">BRIGHT RIVER POWER</span>
    </div>

    <div class="accent-stripe"></div>
    <div class="green-panel"></div>
    <svg class="panel-notch" viewBox="0 0 36 20" aria-hidden="true">
      <polygon points="0,0 36,0 18,18" fill="#f7f7f7"/>
    </svg>

    <div class="contact-person">
      <p class="person-name">Dennis Halvorsen</p>
      <p class="person-role">Chairman</p>
    </div>

    <ul class="contact-list">
      <li class="contact-item">
        <svg class="contact-icon" viewBox="0 0 24 24" aria-hidden="true">
          <rect width="24" height="24" rx="6" fill="#ffffff"/>
          <path d="M8 6.5l2.2 2.4-1.3 1.5c.9 1.8 2.1 3 3.9 3.9l1.5-1.3 2.4 2.2-1.6 1.8c-4.3-.6-8.3-4.6-8.9-8.9z" fill="#5c8d2a"/>
        </svg>
        0438759164
      </li>
      <li class="contact-item">
        <svg class="contact-icon" viewBox="0 0 24 24" aria-hidden="true">
          <rect width="24" height="24" rx="6" fill="#ffffff"/>
          <rect x="5.5" y="7.5" width="13" height="9" rx="1" fill="none" stroke="#5c8d2a" stroke-width="1.6"/>
          <path d="M5.5 8l6.5 5 6.5-5" fill="none" stroke="#5c8d2a" stroke-width="1.6"/>
        </svg>
        info@brightriverpower.net.au
      </li>
      <li class="contact-item">
        <svg class="contact-icon" viewBox="0 0 24 24" aria-hidden="true">
          <rect width="24" height="24" rx="6" fill="#ffffff"/>
          <circle cx="12" cy="12" r="6.5" fill="none" stroke="#5c8d2a" stroke-width="1.5"/>
          <ellipse cx="12" cy="12" rx="2.8" ry="6.5" fill="none" stroke="#5c8d2a" stroke-width="1.2"/>
          <path d="M5.5 12h13" stroke="#5c8d2a" stroke-width="1.2"/>
        </svg>
        www.brightriverpower.net.au
      </li>
    </ul>

    <ul class="services">
      <li class="services-title">Our Services</li>
      <li>Solar</li>
      <li>LED lighting</li>
      <li>Battery storage</li>
      <li>Energy saving solutions</li>
    </ul>
  </main>
</body>
</html>
```